CrestHornSupply.com

I need a new webdesign for a company in the San Jose/SF Bay area that showcases the financial benefits of buying used band instruments for junior high students.This would be opposed to the current and costly option of renting cheap quality instruments from the 2 or 3 local music stores that charge a monthly fee that over the years charges the buyer 3 or 4x over..
Instruments: focus in on Alto Sax, Trumpet, Flute, Clarinet, Trombone, Tenor Sax, Baritone
Target middle schools are Larkfield Middle School and Maple Middle School in San Jose, CA. Both have award winning band programs.
Files attached may or may not be important.
Tabs Needed and funtional
Contact
Shopping Cart
Select Instrument
Checkout
Add to Cart, etc.
Instuments
quantity, etc.
trade in your instrument/sell your instrument
ability to add or take away new instruments for sale. including pictures
Additional questions or info, feel free to ask
Updates
Hi Designers,
Project Deadline Extended
Reason: In the next week you will be receiving specific content that will be required to be had on the website.
New desigins are still welcome. Please continue to contact me if you have questions about your individual designs.
Thanks!
Crest Horn

```html
<!DOCTYPE html>
<html lang="en">
<head>
<meta charset="utf-8">
<title>Crest Horn Supply</title>
<link href="https://fonts.googleapis.com/css2?family=Open+Sans:wght@400;600;700&display=swap" rel="stylesheet">
<style>
:root{
  --red:#e3151b;
  --green:#1aa23a;
  --dark:#1c1c1c;
  --ink:#222;
  --line:#d9d9d9;
  --panel:#ececec;
}
*{box-sizing:border-box;margin:0;padding:0}
html,body{width:802px;height:1200px;overflow:hidden}
body{position:relative;font-family:"Open Sans",Arial,sans-serif;color:var(--ink);
  background:linear-gradient(90deg,#f3f3f3 0,#fff 14%,#fff 86%,#f3f3f3 100%)}
.abs{position:absolute}

/* header */
.brand{left:115px;top:40px;display:flex;align-items:center;gap:8px}
.brand-mark{width:20px;height:20px;border-radius:50%;background:var(--red)}
.brand-name{font-size:23px;font-weight:700;color:var(--dark);line-height:1;white-space:nowrap}
.brand-sub{left:212px;top:68px;font-size:12px;color:var(--green);font-weight:600}
.top-links{top:28px;left:340px;font-size:7.5px;color:#333}
.top-links span{position:absolute;white-space:nowrap}
.top-links .hot{color:var(--red);font-weight:600}
.cart-badge{left:646px;top:16px;width:14px;height:14px;border-radius:50%;background:var(--red);color:#fff;font-size:8px;text-align:center;line-height:14px}
.phone{left:583px;top:53px;display:flex;align-items:center;gap:6px;font-size:15px;color:var(--green);white-space:nowrap}

/* nav */
.nav{left:115px;top:90px;width:572px;height:28px;background:linear-gradient(#4a4a4a,#141414);display:flex}
.nav a{color:#fff;text-decoration:none;font-size:10.5px;font-weight:600;line-height:28px;padding:0 15px;border-right:1px solid #555;white-space:nowrap}
.search{left:523px;top:95px;width:155px;height:18px;background:#fff;border-radius:3px;font-size:7px;color:#999;padding:4px 9px}

/* banner */
.banner{left:115px;top:134px;width:572px;height:243px}
.banner-photo{width:100%;height:203px;background:linear-gradient(#6a7a4a,#c9262c 40%,#e8e0dc 60%,#2a2020)}
.banner-cap{height:40px;background:#e9e7e6;font-size:9.5px;font-weight:600;padding:13px 18px;position:relative;white-space:nowrap}
.arrow-btn{position:absolute;top:10px;width:20px;height:20px;background:#3a3a3a}

/* promo boxes */
.promo{top:402px;width:177px;height:94px;background:linear-gradient(#666,#222);box-shadow:0 8px 10px -6px rgba(0,0,0,.35)}
.promo-head{height:35px;background:linear-gradient(#43c14d,#0f9a2f);color:#fff;text-align:right;padding:6px 8px 0 0;position:relative}
.promo-head::before{content:"";position:absolute;left:-2px;top:-2px;width:52px;height:40px;background:#fff;border-radius:0 0 40px 0}
.promo-head small{display:block;font-size:8.5px;text-align:left;padding-left:56px;line-height:1;white-space:nowrap}
.promo-head b{display:block;font-size:12px;line-height:13px}
.promo-body{color:#fff;font-size:6.5px;line-height:10px;padding:6px 12px 0 12px}
.promo-body i{display:block;font-size:7px;margin-bottom:1px}
.promo-go{position:absolute;right:2px;bottom:-4px;width:18px;height:18px;border-radius:50%;background:#fff}
.promo-go::after{content:"";position:absolute;left:6px;top:5px;border-left:7px solid var(--red);border-top:4px solid transparent;border-bottom:4px solid transparent}

/* featured */
.featured{left:115px;top:525px;width:572px;height:28px;background:var(--panel);color:var(--red);font-size:12px;font-weight:700;padding:6px 11px}
.product{width:130px}
.product-img{height:114px;border:1px solid var(--line);box-shadow:0 1px 3px rgba(0,0,0,.15);background:#fff;display:flex;align-items:center;justify-content:center}
.product-img div{width:70%;height:70%;background:radial-gradient(#e2c15e,#b08b2c 55%,#fff 72%)}
.product-img .dark{background:radial-gradient(#333,#111 50%,#fff 72%)}
.product-img .pale{background:radial-gradient(#f1ead6,#d8ccb0 50%,#fff 72%)}
.stars{margin-top:5px;color:#f5a800;font-size:10px;letter-spacing:1px;line-height:12px;padding-left:1px}
.stars em{color:#bbb;font-style:normal}
.product h3{color:var(--red);font-size:11px;font-weight:700;margin-top:1px;padding-left:1px}
.product p{font-size:6.6px;line-height:10px;padding-left:2px}
.price{font-size:10.5px;font-weight:700;margin-top:6px;padding-left:3px}
.actions{display:flex;gap:4px;margin-top:5px}
.add{width:70px;height:16px;background:linear-gradient(#3c3c3c,#111);border-radius:2px;color:#fff;font-size:6.5px;font-weight:600;line-height:16px;padding-left:11px;position:relative;white-space:nowrap}
.add::before{content:"";position:absolute;left:6px;top:5px;width:8px;height:6px;background:var(--red)}
.add span{padding-left:12px}
.mini{width:16px;height:16px;border:1px solid #bbb;background:#fff}

/* footer */
.foot-line{left:115px;width:572px;height:1px;background:#cfcfcf}
.foot-col h4{color:var(--red);font-size:12px;font-weight:700;margin-bottom:3px;white-space:nowrap}
.foot-col li{list-style:none;font-size:7px;line-height:13px;padding-left:7px;position:relative;white-space:nowrap}
.foot-col li::before{content:"";position:absolute;left:0;top:5px;border-left:3px solid var(--green);border-top:2px solid transparent;border-bottom:2px solid transparent}
.social{left:621px;top:1165px;display:flex;gap:7px}
.social span{width:12px;height:12px;border-radius:50%;background:var(--green)}
</style>
</head>
<body>

<header>
  <div class="abs brand"><span class="brand-mark"></span><span class="brand-name">Crest Horn</span></div>
  <div class="abs brand-sub">Supply</div>

  <nav class="abs top-links" aria-label="Account">
    <span style="left:0">Wish List (0)</span>
    <span style="left:57px">My Account</span>
    <span style="left:113px">Shopping Cart</span>
    <span style="left:177px">Checkout</span>
    <span style="left:225px" class="hot">Login &nbsp;| &nbsp;Register</span>
    <span style="left:330px">$ &#709;</span>
  </nav>
  <svg class="abs" style="left:634px;top:22px" width="22" height="18" viewBox="0 0 22 18" aria-hidden="true"><path d="M1 2h4l3 10h10l2-7H7" fill="none" stroke="#333" stroke-width="1.6"/><circle cx="9" cy="15" r="1.6" fill="#333"/><circle cx="17" cy="15" r="1.6" fill="#333"/></svg>
  <div class="abs cart-badge">0</div>
  <div class="abs phone">
    <svg width="14" height="14" viewBox="0 0 14 14" aria-hidden="true"><circle cx="7" cy="7" r="6" fill="none" stroke="#e3151b" stroke-width="1.5"/><path d="M4.5 4c.5 3 2 4.6 5 5.5l.6-1.3-1.5-.8-.7.7C6.8 7.5 6.4 7 6 5.8l.7-.7-.8-1.5z" fill="#e3151b"/></svg>
    555 01 20 30
  </div>

  <nav class="abs nav" aria-label="Main">
    <a href="#">Home</a><a href="#">About Us</a><a href="#">Instruments</a><a href="#">Buy /Sell</a><a href="#">Contact Us</a>
  </nav>
  <div class="abs search">Search
    <svg class="abs" style="right:12px;top:3px" width="12" height="12" viewBox="0 0 12 12" aria-hidden="true"><circle cx="5" cy="5" r="3.8" fill="none" stroke="#111" stroke-width="1.6"/><path d="M8 8l3 3" stroke="#111" stroke-width="1.8"/></svg>
  </div>
</header>

<section class="abs banner">
  <div class="banner-photo" role="img" aria-label="Student marching band in red and white uniforms holding letter banners"></div>
  <div class="banner-cap">Donec arcu dolor, sodales ut lobortis adipiscing, auctor id purus.
    <span class="arrow-btn" style="left:502px"><svg width="20" height="20" aria-hidden="true"><path d="M12 5l-5 5 5 5" fill="none" stroke="#fff" stroke-width="1.5"/></svg></span>
    <span class="arrow-btn" style="left:525px"><svg width="20" height="20" aria-hidden="true"><path d="M8 5l5 5-5 5" fill="none" stroke="#fff" stroke-width="1.5"/></svg></span>
  </div>
</section>

<section>
  <article class="abs promo" style="left:115px">
    <div class="promo-head"><small>Music News &amp;</small><b>EVENTS</b></div>
    <div class="promo-body"><i>23-Jun-2014</i>Nulla egestas mi non pulvinar sodales. Vesti bulum id luctus augue. Integer sem nisl, susc ipit sit amet cursus non, venenatis</div>
    <span class="promo-go"></span>
  </article>
  <article class="abs promo" style="left:313px">
    <div class="promo-head"><small>Music Teachers</small><b>AVAILABLE</b></div>
    <div class="promo-body" style="padding-top:19px">Nulla egestas mi non pulvinar sodales. Vesti bulum id luctus augue. Integer sem nisl, susc ipit sit amet cursus non, venenatis</div>
    <div class="abs" style="left:40px;top:36px;display:flex;gap:2px" role="img" aria-label="Teacher portraits">
      <span style="width:14px;height:14px;background:#c9a98a"></span><span style="width:14px;height:14px;background:#b88d6c"></span><span style="width:14px;height:14px;background:#d6b99a"></span><span style="width:14px;height:14px;background:#a67b5e"></span><span style="width:14px;height:14px;background:#c4a283"></span>
    </div>
    <span class="promo-go"></span>
  </article>
  <article class="abs promo" style="left:510px">
    <div class="promo-head"><small>Music Products</small><b>HIGHLIGHTS</b></div>
    <div class="promo-body" style="padding-top:8px">Nulla egestas mi non pulvinar sodales. Vesti bulum id luctus augue. Integer sem nisl, susc ipit sit amet cursus non, venenatis Praesent aliquet mauris ante,</div>
    <span class="promo-go"></span>
  </article>
</section>

<h2 class="abs featured">FEATURED PRODUCTS</h2>

<section>
  <div class="abs product" style="left:115px;top:593px"><div class="product-img" role="img" aria-label="Alto saxophone"><div></div></div><div class="stars">★★★<em>☆☆</em></div><h3>Alto Sax</h3><p>vitae adipiscing urna accumsan vitae. Nunc varius nunc ut nisl</p><div class="price">$249.99</div><div class="actions"><span class="add"><span>Add to Cart</span></span><span class="mini"></span><span class="mini"></span></div></div>
  <div class="abs product" style="left:262px;top:593px"><div class="product-img" role="img" aria-label="Trombone"><div></div></div><div class="stars">★★★<em>☆☆</em></div><h3>Trombone</h3><p>vitae adipiscing urna accumsan vitae. Nunc varius nunc ut nisl</p><div class="price">$249.99</div><div class="actions"><span class="add"><span>Add to Cart</span></span><span class="mini"></span><span class="mini"></span></div></div>
  <div class="abs product" style="left:410px;top:593px"><div class="product-img" role="img" aria-label="Clarinet"><div class="dark"></div></div><div class="stars">★★★<em>☆☆</em></div><h3>Clarinet</h3><p>vitae adipiscing urna accumsan vitae. Nunc varius nunc ut nisl</p><div class="price">$249.99</div><div class="actions"><span class="add"><span>Add to Cart</span></span><span class="mini"></span><span class="mini"></span></div></div>
  <div class="abs product" style="left:558px;top:593px"><div class="product-img" role="img" aria-label="Flute"><div class="pale"></div></div><div class="stars">★★★<em>☆☆</em></div><h3>Flute</h3><p>vitae adipiscing urna accumsan vitae. Nunc varius nunc ut nisl</p><div class="price">$249.99</div><div class="actions"><span class="add"><span>Add to Cart</span></span><span class="mini"></span><span class="mini"></span></div></div>

  <div class="abs product" style="left:115px;top:840px"><div class="product-img" role="img" aria-label="Baritone"><div></div></div><div class="stars">★★★<em>☆☆</em></div><h3>Baritone</h3><p>vitae adipiscing urna accumsan vitae. Nunc varius nunc ut nisl</p><div class="price">$249.99</div><div class="actions"><span class="add"><span>Add to Cart</span></span><span class="mini"></span><span class="mini"></span></div></div>
  <div class="abs product" style="left:262px;top:840px"><div class="product-img" role="img" aria-label="Trumpet"><div></div></div><div class="stars">★★★<em>☆☆</em></div><h3>Trumpet</h3><p>vitae adipiscing urna accumsan vitae. Nunc varius nunc ut nisl</p><div class="price">$249.99</div><div class="actions"><span class="add"><span>Add to Cart</span></span><span class="mini"></span><span class="mini"></span></div></div>
  <div class="abs product" style="left:410px;top:840px"><div class="product-img" role="img" aria-label="Tenor saxophone"><div></div></div><div class="stars">★★★<em>☆☆</em></div><h3>Tenor Sax</h3><p>vitae adipiscing urna accumsan vitae. Nunc varius nunc ut nisl</p><div class="price">$249.99</div><div class="actions"><span class="add"><span>Add to Cart</span></span><span class="mini"></span><span class="mini"></span></div></div>
  <div class="abs product" style="left:558px;top:840px"><div class="product-img" role="img" aria-label="Trumpet"><div></div></div><div class="stars">★★★<em>☆☆</em></div><h3>Trumpet</h3><p>vitae adipiscing urna accumsan vitae. Nunc varius nunc ut nisl</p><div class="price">$249.99</div><div class="actions"><span class="add"><span>Add to Cart</span></span><span class="mini"></span><span class="mini"></span></div></div>
</section>

<footer>
  <div class="abs foot-line" style="top:1088px"></div>
  <div class="abs foot-col" style="left:117px;top:1101px"><h4>Information</h4><ul><li>About</li><li>Delivery</li><li>Privacy Policy</li><li>Terms &amp; Conditions</li></ul></div>
  <div class="abs foot-col" style="left:215px;top:1101px"><h4>Customer Service</h4><ul><li>Contact Us</li><li>Returns</li><li>Site Map</li></ul></div>
  <div class="abs foot-col" style="left:347px;top:1101px"><h4>Extras</h4><ul><li>Brands</li><li>Gift Vouchers</li><li>Affiliates</li><li>Specials</li></ul></div>
  <div class="abs foot-col" style="left:428px;top:1101px"><h4>My Account</h4><ul><li>My Account</li><li>Order History</li><li>Wish List</li><li>Newsletter</li></ul></div>
  <div class="abs brand" style="left:545px;top:1120px"><span class="brand-mark" style="width:18px;height:18px"></span><span class="brand-name" style="font-size:20px">Crest Horn</span></div>
  <div class="abs brand-sub" style="left:625px;top:1143px;font-size:11px">Supply</div>
  <div class="abs social" aria-label="Social links"><span></span><span></span><span></span><span></span></div>
  <div class="abs foot-line" style="top:1197px"></div>
</footer>

</body>
</html>
```